Website redesign for job agency recruitment

Please refer to the attached document, “Tarvenly Work Website Brief,” for comprehensive details regarding the scope, objectives, and requirements of this website redesign project.

For imagery you can use images from this website https://www.pixelmarrowfoto.com or any other you regularly use.

Target Market(s)

Jobseekers and Companies looking for general labour

Industry/Entity Type

Services: Oil, Gas and Mining, Administrative, Construction and Trades, Warehouse and Logistics and, Manufacturing.

Number of Pages Required

5+ page

Font styles to use
Serif
Other font styles liked:
• Inter, Open-Sans or similar.

Requirements
Must have
• The requirements highlighted in the Word document attached. The final design needs to be provided in Figma including all viewports (Desktop, mobiel and tablet)
Should not have
• Website we like as a reference: www.brevicktalentco.com, www.qelvaworks.com, www.zunmarra.com, www.ferrowhires.com, www.9vtalentpool.com, www.hiringwithtrello.ca

```html
<!DOCTYPE html>
<html lang="en">
<head>
<meta charset="utf-8">
<title>Tarvenly Work Agency Ltd.</title>
<link href="https://fonts.googleapis.com/css2?family=Lato:ital,wght@0,400;0,700;0,900;1,400;1,700&display=swap" rel="stylesheet">
<style>
:root{
  --blue:#1b3b9e;
  --blue-dark:#142d7d;
  --yellow:#f6b800;
  --ink:#111318;
  --muted:#a3a6ad;
  --mist:#f1f1f5;
  --arc:#e3e6ee;
  --white:#ffffff;
  --black:#000000;
}
*{margin:0;padding:0;box-sizing:border-box}
html,body{width:1200px;height:2830px;overflow:hidden;background:var(--white)}
body{font-family:'Lato',sans-serif;color:var(--ink);position:relative}
.abs{position:absolute}

/* header */
.site-header{position:absolute;top:0;left:0;width:1200px;height:79px;background:var(--white);z-index:5;box-shadow:0 2px 6px rgba(0,0,0,.08)}
.site-header::before{content:"";position:absolute;top:0;left:0;width:600px;height:3px;background:var(--yellow)}
.site-header::after{content:"";position:absolute;top:0;left:600px;width:600px;height:3px;background:var(--blue)}
.brand-badge{position:absolute;left:66px;top:0;width:234px;height:165px;background:var(--white);border-radius:0 0 117px 117px/0 0 70px 70px;box-shadow:0 4px 10px rgba(0,0,0,.12);z-index:6;display:flex;flex-direction:column;align-items:center;justify-content:center;gap:8px}
.brand-badge .mark{width:46px;height:46px;border-radius:50%;background:var(--blue)}
.brand-badge .name{font-size:14px;font-weight:700;color:var(--blue)}
.main-nav a{position:absolute;top:34px;font-size:15px;color:var(--ink);text-decoration:none}
.main-nav a.active{color:var(--blue);font-weight:700}
.quote-btn{position:absolute;left:971px;top:22px;width:117px;height:38px;border-radius:19px;background:var(--yellow);font-weight:700;font-size:15px;display:flex;align-items:center;justify-content:center;color:var(--ink)}

/* hero */
.hero{position:absolute;top:79px;left:0;width:1200px;height:700px}
.hero-photo{position:absolute;inset:0;background:linear-gradient(100deg,#f4f3f1 0%,#e9e4dc 30%,#c9a774 48%,#d8902c 62%,#f0b640 75%,#7a5a30 100%)}
.hero h1{position:absolute;left:110px;top:174px;font-size:48px;font-weight:700;line-height:58px;color:var(--ink)}
.hero p{position:absolute;left:111px;top:300px;width:420px;font-size:16px;line-height:25.7px;font-weight:700}
.btn{position:absolute;height:57px;border-radius:29px;display:flex;align-items:center;justify-content:center;font-size:17px;font-weight:700}
.btn-blue{background:var(--blue);color:var(--white);border:2px solid var(--white)}
.btn-yellow{background:var(--yellow);color:var(--ink);border:2px solid var(--white)}
.hero-curve{position:absolute;left:0;top:600px;z-index:2}
.scroll-down{position:absolute;left:566px;top:707px;width:66px;height:66px;border-radius:50%;background:var(--white);box-shadow:0 3px 10px rgba(0,0,0,.15);z-index:3;display:flex;align-items:center;justify-content:center}

/* services */
.services-arcs{position:absolute;left:0;top:880px}
.offer-title{position:absolute;left:143px;top:1214px;transform:translate(-50%,-50%) rotate(-90deg);font-size:44px;font-weight:700;color:var(--blue);white-space:nowrap}
.offer-bar{position:absolute;left:182px;top:1187px;width:5px;height:52px;background:var(--blue)}
.service{position:absolute;font-size:22px;line-height:30px;color:var(--muted)}
.service.active{font-size:28px;font-weight:700;color:var(--ink)}
.service-copy{position:absolute;left:600px;width:488px;font-size:15px;line-height:25.7px;text-align:justify}
.photo-card{position:absolute;left:600px;width:488px;border-radius:32px}

/* about */
.about-bg{position:absolute;left:0;top:1655px}
.about-photo{position:absolute;left:112px;top:1798px;width:450px;height:450px;border-radius:50%;background:radial-gradient(circle at 50% 45%,#e9e5dd 0%,#b9c6d6 55%,#8da3bd 100%)}
.about h2{position:absolute;left:642px;top:1778px;font-size:44px;font-weight:700;color:var(--blue)}
.about .rule{position:absolute;left:642px;top:1841px;width:53px;height:4px;background:var(--blue)}
.about p{position:absolute;left:642px;width:446px;font-size:14.6px;letter-spacing:-0.1px;line-height:25.7px;text-align:justify}
.read-more{left:643px;top:2189px;width:135px;height:55px}

/* footer */
.footer-bg{position:absolute;left:0;top:2250px}
.footer-brand{position:absolute;left:110px;top:2640px;display:flex;align-items:center;gap:12px}
.footer-brand .mark{width:30px;height:30px;border-radius:50%;background:var(--yellow)}
.footer-brand .name{font-size:22px;color:var(--white)}
.footer-tag{position:absolute;left:111px;top:2683px;font-size:14px;font-style:italic;color:var(--white)}
.footer-col h3{position:absolute;font-size:22px;font-weight:400;color:var(--white)}
.footer-col li{position:absolute;list-style:none;font-size:15.5px;color:var(--white);display:flex;align-items:center;gap:10px}
.contact-item{position:absolute;left:890px;display:flex;align-items:center;gap:14px;color:var(--white);font-size:15.5px;line-height:27px}
.contact-item .ico{width:34px;height:34px;border-radius:50%;background:var(--white);display:flex;align-items:center;justify-content:center;flex:none}
.footer-rule{position:absolute;left:110px;top:2744px;width:978px;height:1px;background:#3a3a3a}
.copyright{position:absolute;left:0;top:2772px;width:1200px;text-align:center;color:var(--white);font-weight:700;font-size:16px}
</style>
</head>
<body>

<header class="site-header">
  <nav class="main-nav">
    <a class="active" style="left:398px">Home</a>
    <a style="left:487px">Candidates</a>
    <a style="left:614px">About Us</a>
    <a style="left:728px">Contact</a>
    <a style="left:833px">Forms &amp; Links</a>
  </nav>
  <div class="quote-btn">Get a Quote</div>
</header>
<div class="brand-badge">
  <div class="mark"></div>
  <div class="name">Tarvenly Work Agency Ltd.</div>
</div>

<section class="hero">
  <div class="hero-photo" role="img" aria-label="Glass office tower reflecting a golden sunset over a city skyline"></div>
  <h1>The Right People<br>to Power Your Business</h1>
  <p>Connecting top talent with leading employers in Oil, Gas &amp; Mining, Administrative Support, Construction &amp; Trades, Logistics, Warehousing, and Manufacturing.</p>
  <div class="btn btn-blue" style="left:111px;top:396px;width:162px">For Candidates</div>
  <div class="btn btn-yellow" style="left:297px;top:396px;width:162px">For Employers</div>
</section>
<svg class="hero-curve" width="1200" height="200" viewBox="0 600 1200 200">
  <path d="M0,620 Q560,850 1200,640 L1200,800 L0,800 Z" fill="#ffffff"/>
  <path d="M80,662 Q560,820 1200,612" fill="none" stroke="#f6b800" stroke-width="7"/>
</svg>
<div class="scroll-down">
  <svg width="40" height="40" viewBox="0 0 40 40"><circle cx="20" cy="20" r="17" fill="none" stroke="#1b3b9e" stroke-width="2.5"/><path d="M20 11v17M13 21l7 7 7-7" fill="none" stroke="#1b3b9e" stroke-width="2.5" stroke-linecap="round" stroke-linejoin="round"/></svg>
</div>

<section class="services">
  <svg class="services-arcs" width="380" height="660" viewBox="0 880 380 660">
    <path d="M190,915 C330,960 380,1250 250,1450 C180,1540 60,1545 10,1480 C120,1520 250,1430 300,1250 C340,1080 290,950 190,915 Z" fill="#e3e6ee"/>
    <path d="M0,1060 C40,940 180,870 250,930 C310,1000 320,1150 292,1255 C300,1120 280,990 230,960 C160,920 60,980 0,1070 Z" fill="#f6b800"/>
  </svg>
  <div class="offer-title">What We Offer</div>
  <div class="offer-bar"></div>
  <div class="service active" style="left:214px;top:866px">Oil, Gas &amp; Mining »</div>
  <div class="service" style="left:346px;top:993px">Administrative</div>
  <div class="service" style="left:377px;top:1133px">Construction<br>and Trades</div>
  <div class="service" style="left:377px;top:1290px">Warehouse and<br>Logistics</div>
  <div class="service" style="left:319px;top:1461px">Manufacturing</div>

  <p class="service-copy" style="top:866px">As a specialist Division participating solely in the Oil, Gas &amp; Mining industry, we continuously meet the challenging staffing demands of Resource companies, Engineering Consultancies, Production sites, Drilling/Exploration companies and Specialty Products.</p>
  <p class="service-copy" style="top:995px">Tarvenly Work Agency is a premiere Oil, Gas &amp; Mining staffing agency that can provide you with a reliable and experienced workforce. From rig hands to engineers, we provide solutions from temp, temp-to-hire, and permanent positions.</p>
  <div class="photo-card" style="top:1126px;height:222px;background:linear-gradient(90deg,#f2c46a 0%,#e08a2a 45%,#3a2a20 100%)" role="img" aria-label="Two workers silhouetted beside industrial pipelines at sunset"></div>
  <div class="photo-card" style="top:1363px;height:173px;background:linear-gradient(90deg,#3b4a6a 0%,#e79a34 50%,#2a3150 100%)" role="img" aria-label="Crew working on a drilling rig against the evening sun"></div>
</section>

<section class="about">
  <svg class="about-bg" width="1200" height="720" viewBox="0 1655 1200 720">
    <path d="M0,1795 Q600,1580 1200,1765 L1200,2270 L0,2270 Z" fill="#f1f1f5"/>
    <path d="M0,1802 Q560,1580 1110,1753" fill="none" stroke="#f6b800" stroke-width="8"/>
    <path d="M0,2270 L0,2262 Q600,2415 1200,2262 L1200,2375 L0,2375 Z" fill="#000000"/>
    <path d="M110,2300 Q600,2465 1200,2252" fill="none" stroke="#f6b800" stroke-width="8"/>
    <path d="M335,1776 A246,246 0 0 1 335,2268" fill="none" stroke="#1b3b9e" stroke-width="10" transform="translate(10,0)"/>
    <path d="M335,2268 A246,246 0 0 1 335,1776" fill="none" stroke="#f6b800" stroke-width="8" transform="translate(-10,0)"/>
  </svg>
  <div class="about-photo" role="img" aria-label="Group of smiling office colleagues standing together"></div>
  <h2>About Tarvenly Work</h2>
  <div class="rule"></div>
  <p style="top:1864px">Tarvenly Work Agency offers a complete range of staffing services to keep pace with your career or operational demands. We understand it's not only daunting but very costly in both time and money to make your business thrive in a rapidly changing environment.</p>
  <p style="top:2019px">Our staffing and recruitment services are not just limited to finding good people. We are a Canada-wide team of capable search specialists, career counselors, HR specialists, and business consultants who enjoy providing our clients with a very customized staffing solution that evolves within their market. Each project provides a chance for us to apply our knowledge and shine.</p>
  <div class="btn btn-yellow read-more">Read More</div>
</section>

<footer class="site-footer">
  <div class="abs" style="left:0;top:2375px;width:1200px;height:455px;background:var(--black)"></div>
  <div class="footer-brand"><div class="mark"></div><div class="name">Tarvenly Work Agency Ltd.</div></div>
  <div class="footer-tag">The right <b>people</b> to power your business</div>

  <div class="footer-col">
    <h3 style="left:463px;top:2484px">Quick Links</h3>
    <ul>
      <li style="left:463px;top:2530px"><svg width="14" height="12" viewBox="0 0 14 12"><path d="M0 4h7V0l7 6-7 6V8H0z" fill="#fff"/></svg>Home</li>
      <li style="left:463px;top:2564px"><svg width="14" height="12" viewBox="0 0 14 12"><path d="M0 4h7V0l7 6-7 6V8H0z" fill="#fff"/></svg>Candidates</li>
      <li style="left:463px;top:2598px"><svg width="14" height="12" viewBox="0 0 14 12"><path d="M0 4h7V0l7 6-7 6V8H0z" fill="#fff"/></svg>Companies</li>
      <li style="left:463px;top:2632px"><svg width="14" height="12" viewBox="0 0 14 12"><path d="M0 4h7V0l7 6-7 6V8H0z" fill="#fff"/></svg>About</li>
      <li style="left:463px;top:2666px"><svg width="14" height="12" viewBox="0 0 14 12"><path d="M0 4h7V0l7 6-7 6V8H0z" fill="#fff"/></svg>Contact Us</li>
    </ul>
  </div>
  <div class="footer-col">
    <h3 style="left:678px;top:2484px">Help Links</h3>
    <ul>
      <li style="left:678px;top:2530px"><svg width="14" height="12" viewBox="0 0 14 12"><path d="M0 4h7V0l7 6-7 6V8H0z" fill="#fff"/></svg>FAQ</li>
      <li style="left:678px;top:2564px"><svg width="14" height="12" viewBox="0 0 14 12"><path d="M0 4h7V0l7 6-7 6V8H0z" fill="#fff"/></svg>Terms of use</li>
      <li style="left:678px;top:2598px"><svg width="14" height="12" viewBox="0 0 14 12"><path d="M0 4h7V0l7 6-7 6V8H0z" fill="#fff"/></svg>Privacy Policy</li>
      <li style="left:678px;top:2632px"><svg width="14" height="12" viewBox="0 0 14 12"><path d="M0 4h7V0l7 6-7 6V8H0z" fill="#fff"/></svg>Support Links</li>
      <li style="left:678px;top:2666px"><svg width="14" height="12" viewBox="0 0 14 12"><path d="M0 4h7V0l7 6-7 6V8H0z" fill="#fff"/></svg>Conditions</li>
    </ul>
  </div>
  <div class="footer-col">
    <h3 style="left:890px;top:2484px">Contact Us</h3>
  </div>
  <div class="contact-item" style="top:2528px">
    <span class="ico"><svg width="16" height="20" viewBox="0 0 16 20"><path d="M8 0a8 8 0 0 0-8 8c0 6 8 12 8 12s8-6 8-12a8 8 0 0 0-8-8zm0 11a3 3 0 1 1 0-6 3 3 0 0 1 0 6z" fill="#000"/></svg></span>
    <span>Tarvenly Work Agency<br>United States</span>
  </div>
  <div class="contact-item" style="top:2597px">
    <span class="ico"><svg width="18" height="18" viewBox="0 0 24 24"><path d="M6.6 10.8a15 15 0 0 0 6.6 6.6l2.2-2.2c.3-.3.7-.4 1-.2 1.1.4 2.3.6 3.6.6.6 0 1 .4 1 1V20c0 .6-.4 1-1 1C10.6 21 3 13.4 3 4c0-.6.4-1 1-1h3.5c.6 0 1 .4 1 1 0 1.3.2 2.5.6 3.6.1.3 0 .7-.2 1z" fill="#000"/></svg></span>
    <span>+1-888-555-0142</span>
  </div>
  <div class="contact-item" style="top:2650px">
    <span class="ico"><svg width="18" height="14" viewBox="0 0 18 14"><path d="M0 0h18v14H0z" fill="#000"/><path d="M1 1l8 6 8-6" fill="none" stroke="#fff" stroke-width="1.6"/></svg></span>
    <span>info@tarvenlywork.com</span>
  </div>
  <div class="footer-rule"></div>
  <div class="copyright">Copyrights@2026.Tarvenly Work Agency.All Rights Reserved</div>
</footer>

</body>
</html>
```